Coastal Learner Bureau business cards

Australian company about to start offering its services. We recruit international students to come to study English, vocational education and postgraduate courses in Australia. We help them find the institution and select the right city they want to come to Australia. We are a young, online oriented and supportive agency. Our clients are between 18 and 35 years old, mainly University students, young professionals or people with work experience. We provide much more information that any other agency offer. We administrate a Facebook group with more than 11.000 members that daily ask questions about general information when coming to Australia, while they are here and even after they leave the country

Target Market(s)

International students from South America, Central America and Europe

Industry/Entity Type

Student

Contact Information for Business Card

Tomas Bilbrea
Managing Director
tomas@kelvarin.com.au
www.kelvoria.com.au
+61 491058264
Melbourne, Australia

Font styles to use
Serif
Sans Serif

Colors

Designer to choose colors to be used in the design.

Requirements
Must have
• Horizontal design
• Standard business card size and shape. If font uses green or yellow colours, they will have to match the ones from the logo
Nice to have
• UPDATE: Use the contents of the green image to design one of the card sides. Use our logo in the background of that side as watermark.
• Passport image, or immigration stamps. A picture of the Yarra River (from Melbourne) would be cool as well.
Should not have
• Non-standard business card size and shape
• Not black as the background colour of any sides as we are not a VIP agency or a hight class service. We are orientes to young people and they like colours, pictures, something attractive.
• Vertical design
• NO YELLOW or BLACK AS THE BACKGROUND COLOUR OF ANY SIDE OF THE BIZ CARD

```html
<!DOCTYPE html>
<html lang="en">
<head>
<meta charset="utf-8">
<title>Coastal Learner Bureau – Business Cards</title>
<link rel="stylesheet" href="https://fonts.googleapis.com/css2?family=Jost:wght@400;500&family=Oswald:wght@500&display=swap">
<style>
  :root {
    --brand-green: #0e6b45;
    --brand-yellow: #e6b824;
    --paper: #ffffff;
    --stage: #e9e7e2;
    --sky: #9cc3e6;
    --river: #3f6f9c;
    --park: #4f7d3a;
    --text-green: #0e5a3a;
  }
  * { box-sizing: border-box; margin: 0; padding: 0; }
  html, body {
    width: 1200px;
    height: 1000px;
    overflow: hidden;
    background: var(--stage);
    font-family: "Jost", sans-serif;
  }
  .sheet {
    position: relative;
    width: 1200px;
    height: 1000px;
  }
  .card {
    position: absolute;
    left: 270px;
    width: 660px;
    height: 377px;
    background: var(--paper);
    box-shadow: 0 6px 22px rgba(0, 0, 0, 0.14);
    overflow: hidden;
  }
  .card--front { top: 96px; padding: 18px; }
  .card--back { top: 527px; }

  .city-photo {
    width: 100%;
    height: 100%;
    background:
      linear-gradient(180deg, transparent 55%, rgba(63, 111, 156, 0.9) 70%, var(--river) 100%),
      linear-gradient(115deg, #f6edc8 0%, var(--sky) 30%, #5f88b8 60%, var(--park) 100%);
  }

  .card-art { position: absolute; inset: 0; width: 660px; height: 377px; }

  .brand {
    position: absolute;
    left: 52px;
    top: 56px;
    display: flex;
    align-items: center;
    gap: 10px;
    color: var(--brand-green);
    font-weight: 500;
    font-size: 30px;
    letter-spacing: 0.5px;
  }
  .brand-dot {
    width: 14px;
    height: 14px;
    border-radius: 50%;
    background: var(--brand-yellow);
  }

  .contact-list {
    position: absolute;
    left: 40px;
    top: 250px;
    list-style: none;
    color: var(--text-green);
    font-size: 16px;
    line-height: 25px;
    letter-spacing: 0.4px;
  }
  .contact-list li { display: flex; align-items: center; gap: 10px; }
  .contact-icon { width: 12px; height: 12px; flex: none; }

  .holder {
    position: absolute;
    right: 40px;
    top: 118px;
    text-align: right;
    color: var(--paper);
  }
  .holder-name {
    font-family: "Oswald", sans-serif;
    font-weight: 500;
    font-size: 29px;
    letter-spacing: 2px;
    color: var(--brand-yellow);
    text-transform: uppercase;
    line-height: 1.1;
  }
  .holder-role { font-size: 20px; letter-spacing: 0.5px; }

  .location {
    position: absolute;
    right: 80px;
    top: 288px;
    text-align: center;
    color: var(--paper);
    font-size: 18px;
    line-height: 24px;
    letter-spacing: 0.5px;
  }
</style>
</head>
<body>
<main class="sheet">
  <section class="card card--front" aria-label="Card front">
    <div class="city-photo" role="img" aria-label="Photograph of the Yarra River and the Melbourne city skyline at sunrise"></div>
  </section>

  <section class="card card--back" aria-label="Card back">
    <svg class="card-art" viewBox="0 0 660 377" aria-hidden="true">
      <path d="M300 0 L660 0 L660 377 L332 377 Q430 190 300 0 Z" fill="var(--brand-green)"/>
      <path d="M287 -4 Q416 190 318 381" fill="none" stroke="var(--brand-yellow)" stroke-width="8"/>
    </svg>

    <div class="brand"><span class="brand-dot"></span>Kelvoria</div>

    <ul class="contact-list">
      <li>
        <svg class="contact-icon" viewBox="0 0 12 12"><rect x="3" y="0.5" width="6" height="11" rx="1" fill="none" stroke="var(--brand-green)" stroke-width="1.2"/></svg>
        +61 491058264
      </li>
      <li>
        <svg class="contact-icon" viewBox="0 0 12 12"><rect x="0.5" y="2" width="11" height="8" fill="var(--brand-green)"/><path d="M0.5 2 L6 6.5 L11.5 2" fill="none" stroke="#fff" stroke-width="1"/></svg>
        tomas@kelvarin.com.au
      </li>
      <li>
        <svg class="contact-icon" viewBox="0 0 12 12"><circle cx="5" cy="5" r="3.6" fill="none" stroke="var(--brand-green)" stroke-width="1.6"/><path d="M7.6 7.6 L11 11" stroke="var(--brand-green)" stroke-width="1.8"/></svg>
        www.kelvoria.com.au
      </li>
    </ul>

    <div class="holder">
      <p class="holder-name">Tomas Bilbrea</p>
      <p class="holder-role">Managing Director</p>
    </div>

    <p class="location">Melbourne,<br>Australia</p>
  </section>
</main>
</body>
</html>
```